Business Card Design

Tumble Harbor is a Laundromat Store
we provide wash and Fold service to Customers who are busy with their life and can not come to the store and do laundry
we have customers who drop their laundry at the store
but now i want to provide service to customers who are not able to come to the store to drop. i will go to their address and pickup the laundry and get it washed folded and delivered
Updates
Can you use the colour in you design which i uploaded and also fusha fluorescent green bright pink
Target Market(s)
all works of life who don't have time to do laundry
Industry/Entity Type
Store
Contact Information for Business Card
TumbleHarbor Laundromat
247 Mallory Street
Lynn MA 01938
Look and feel
Each slider illustrates characteristics of the customer's brand and the style your logo design should communicate.

```html
<!DOCTYPE html>
<html lang="en">
<head>
<meta charset="UTF-8">
<title>TumbleHarbor Laundromat – Business Card</title>
<link href="https://fonts.googleapis.com/css2?family=Lato:wght@400;700;900&display=swap" rel="stylesheet">
<style>
  :root {
    --backdrop: #2e2e2e;
    --pink: #e8198b;
    --pink-deep: #c80f74;
    --purple: #8a2a8e;
    --green: #1bb865;
    --green-deep: #0c7f42;
    --teal-edge: #3fb6c8;
    --white: #ffffff;
    --ring: #e6e6e6;
  }
  * { box-sizing: border-box; margin: 0; padding: 0; }
  html, body {
    width: 1200px;
    height: 900px;
    overflow: hidden;
    background: var(--backdrop);
    font-family: "Lato", Arial, sans-serif;
  }
  .card {
    position: absolute;
    left: 60px;
    top: 130px;
    width: 1080px;
    height: 640px;
    background: radial-gradient(ellipse at 50% 35%, var(--pink) 0%, var(--pink-deep) 100%);
    overflow: hidden;
    box-shadow: 0 20px 50px rgba(0,0,0,0.45);
  }
  .brand {
    position: absolute;
    top: 30px;
    left: 0;
    width: 100%;
    text-align: center;
    color: var(--white);
    font-weight: 900;
    font-size: 42px;
    line-height: 1.2;
  }
  .call {
    position: absolute;
    top: 96px;
    left: 50%;
    transform: translateX(-50%);
    background: var(--purple);
    color: var(--white);
    font-weight: 700;
    font-size: 28px;
    line-height: 1.2;
    padding: 5px 16px;
    white-space: nowrap;
  }
  .address {
    position: absolute;
    top: 150px;
    left: 0;
    width: 100%;
    text-align: center;
    color: var(--white);
    font-weight: 700;
    font-size: 24px;
    letter-spacing: 4px;
  }
  .photo { position: absolute; }
  .photo--dirty {
    left: 300px;
    top: 200px;
    width: 230px;
    height: 170px;
    border-radius: 50% 50% 10px 10px / 60% 60% 10px 10px;
    background: linear-gradient(135deg, #b4879f, #8f6a86 50%, #c6a0a8);
  }
  .photo--clean {
    left: 640px;
    top: 195px;
    width: 180px;
    height: 175px;
    border-radius: 8px;
    background: linear-gradient(180deg, #6a5a78, #b34a4a 35%, #3f4a68 60%, #8a3f3f 85%, #5a4c5a);
  }
  .from-to {
    position: absolute;
    left: 470px;
    top: 198px;
    width: 150px;
    height: 150px;
    border-radius: 50%;
    background: var(--purple);
    color: var(--white);
    font-weight: 700;
    text-align: center;
    z-index: 1;
  }
  .from-to__from,
  .from-to__to {
    position: absolute;
    left: 0;
    width: 100%;
    font-size: 28px;
    line-height: 1;
  }
  .from-to__from { top: 30px; }
  .from-to__to { top: 96px; font-weight: 900; }
  .from-to svg { position: absolute; left: 25px; top: 66px; }
  .band { position: absolute; left: 0; top: 0; z-index: 2; }
  .steps {
    position: absolute;
    left: 0;
    top: 0;
    width: 1080px;
    height: 640px;
    z-index: 3;
  }
  .step {
    position: absolute;
    width: 240px;
    text-align: center;
    color: var(--white);
    font-weight: 700;
    font-size: 20px;
    line-height: 1.2;
  }
  .step__icon {
    width: 100px;
    height: 100px;
    margin: 0 auto 10px;
    border-radius: 50%;
    background: var(--white);
    border: 4px solid var(--ring);
    display: flex;
    align-items: center;
    justify-content: center;
  }
  .step__art { width: 64px; height: 64px; border-radius: 50%; }
  .step--schedule { left: 20px; top: 455px; }
  .step--pickup { left: 290px; top: 430px; }
  .step--wash { left: 560px; top: 410px; }
  .step--enjoy { left: 800px; top: 400px; }
  .step--schedule .step__art { background: linear-gradient(180deg, #444, #d9d9d9); border-radius: 8px; }
  .step--pickup .step__art { background: linear-gradient(180deg, #d94a3a 40%, #4a9ad9 40%); border-radius: 8px; }
  .step--wash .step__art { background: linear-gradient(135deg, #9a8a6a, #5a6a7a); border-radius: 8px; }
  .step--enjoy .step__art { background: radial-gradient(circle, #ffe14a, #f2b90f); }
</style>
</head>
<body>
  <main class="card">
    <div class="brand">TumbleHarbor Laundromat</div>
    <div class="call">CALL US: 079 555 01234</div>
    <div class="address">247 MALLORY STREET LYNN MA 01938</div>

    <div class="photo photo--dirty" role="img" aria-label="Pile of crumpled dirty laundry"></div>
    <div class="photo photo--clean" role="img" aria-label="Neat stack of folded clean clothes"></div>

    <div class="from-to">
      <span class="from-to__from">FROM</span>
      <svg width="100" height="20" viewBox="0 0 100 20" aria-hidden="true">
        <g stroke="#ffffff" stroke-width="2" fill="none">
          <line x1="6" y1="6" x2="94" y2="6"/><polyline points="86,1 94,6 86,11"/>
          <line x1="6" y1="14" x2="94" y2="14"/><polyline points="14,9 6,14 14,19"/>
        </g>
      </svg>
      <span class="from-to__to">TO</span>
    </div>

    <svg class="band" width="1080" height="640" viewBox="0 0 1080 640" aria-hidden="true">
      <defs>
        <linearGradient id="bandFill" x1="0" y1="0" x2="0" y2="1">
          <stop offset="0" stop-color="#1bb865"/>
          <stop offset="1" stop-color="#0c7f42"/>
        </linearGradient>
      </defs>
      <path d="M0 440 Q540 290 1080 420 L1080 640 L0 640 Z" fill="url(#bandFill)"/>
      <path d="M0 440 Q540 290 1080 420" fill="none" stroke="#3fb6c8" stroke-width="6"/>
      <g stroke="#ffffff" stroke-width="3" fill="none" stroke-linecap="round">
        <path d="M205 515 Q265 475 345 482"/><polyline points="335,474 345,482 335,490"/>
        <path d="M475 490 Q535 452 615 460"/><polyline points="605,452 615,460 605,468"/>
        <path d="M745 468 Q795 440 855 450"/><polyline points="845,442 855,450 845,458"/>
      </g>
    </svg>

    <div class="steps">
      <div class="step step--schedule">
        <div class="step__icon"><div class="step__art" role="img" aria-label="Schedule calendar sheet"></div></div>
        You Schedule<br>A Pick-Up
      </div>
      <div class="step step--pickup">
        <div class="step__icon"><div class="step__art" role="img" aria-label="Small house"></div></div>
        We Pick-Up<br>Your Dirty Laundry
      </div>
      <div class="step step--wash">
        <div class="step__icon"><div class="step__art" role="img" aria-label="Washing machines and dryers"></div></div>
        We Wash, Dry, Fold<br>&amp; Return Clean Laundry
      </div>
      <div class="step step--enjoy">
        <div class="step__icon"><div class="step__art" role="img" aria-label="Happy yellow emoticon giving thumbs up"></div></div>
        Enjoy Effortless<br>Clean Laundry
      </div>
    </div>
  </main>
</body>
</html>
```